Modern Business Card

Modern professional business card with more than just logo and demographic info. Something memorable.

We are a trendy/modern chiropractic group with an emphasis on neurology, hence the minimalist-type brain logo. We want to convey that modern and technical aspect with professionalism and the elite nature of our practice environment.

```html
<!DOCTYPE html>
<html lang="en">
<head>
<meta charset="UTF-8">
<title>Cortexa Spine – Business Card</title>
<link rel="stylesheet" href="https://fonts.googleapis.com/css2?family=Tinos:wght@400;700&display=swap">
<style>
  :root {
    --stage: #2e2e2f;
    --card: #141415;
    --card-edge: #1d1d1f;
    --front-mark: #5d5d62;
    --accent: #4a78c4;
    --ink: #f2f2f2;
    --ink-soft: #c9c9cc;
  }
  * { margin: 0; padding: 0; box-sizing: border-box; }
  html, body {
    width: 800px;
    height: 1200px;
    overflow: hidden;
    background: var(--stage);
    font-family: "Tinos", "Times New Roman", serif;
  }
  .canvas {
    width: 800px;
    height: 1200px;
    display: flex;
    flex-direction: column;
    align-items: center;
    justify-content: center;
    gap: 110px;
  }
  .card {
    position: relative;
    width: 640px;
    height: 366px;
    background: var(--card);
    border: 1px solid var(--card-edge);
    border-radius: 3px;
  }

  /* Front side */
  .card-front {
    display: flex;
    align-items: center;
    justify-content: center;
  }
  .front-name {
    color: var(--front-mark);
    font-size: 46px;
    font-weight: 700;
    letter-spacing: 6px;
    text-transform: uppercase;
  }

  /* Back side */
  .card-back { overflow: hidden; }
  .back-mark {
    position: absolute;
    left: 40px;
    top: 100px;
    width: 240px;
    color: var(--accent);
    font-size: 40px;
    font-weight: 700;
    line-height: 1.1;
    letter-spacing: 2px;
    text-transform: uppercase;
  }
  .back-mark-square {
    display: block;
    width: 22px;
    height: 22px;
    margin-bottom: 18px;
    background: var(--accent);
  }
  .details {
    position: absolute;
    left: 318px;
    top: 84px;
    color: var(--ink);
  }
  .wordmark {
    font-size: 30px;
    font-weight: 400;
    letter-spacing: 1.5px;
    line-height: 1;
    text-transform: uppercase;
  }
  .wordmark-sub {
    display: block;
    font-size: 19px;
    letter-spacing: 2px;
    margin-top: 2px;
  }
  .person { margin-top: 22px; }
  .person-name {
    color: var(--accent);
    font-size: 19px;
    line-height: 1.2;
  }
  .person-role {
    color: var(--ink-soft);
    font-size: 13px;
    margin-top: 2px;
  }
  .contact-list {
    list-style: none;
    margin-top: 16px;
    font-size: 13px;
    line-height: 1.55;
    color: var(--ink-soft);
  }
  .contact-list li {
    display: flex;
    align-items: center;
    gap: 10px;
  }
  .contact-icon {
    width: 9px;
    height: 9px;
    background: var(--accent);
    flex: none;
  }
  .address {
    margin-top: 8px;
    font-size: 13px;
    line-height: 1.45;
    color: var(--ink-soft);
  }
</style>
</head>
<body>
  <main class="canvas">
    <section class="card card-front" aria-label="Card front">
      <span class="front-name">Cortexa Spine</span>
    </section>

    <section class="card card-back" aria-label="Card back">
      <div class="back-mark">
        <span class="back-mark-square"></span>
        Cortexa<br>Spine
      </div>

      <div class="details">
        <h1 class="wordmark">Cortexa<span class="wordmark-sub">Spine</span></h1>

        <div class="person">
          <p class="person-name">Lena Marlowe Price</p>
          <p class="person-role">Managing Director</p>
        </div>

        <ul class="contact-list">
          <li><span class="contact-icon"></span>555-014-2270</li>
          <li><span class="contact-icon"></span>lena@cortexaspine.com</li>
          <li><span class="contact-icon"></span>www.cortexaspine.com</li>
        </ul>

        <p class="address">88 Meridian Ave., Fairview,<br>Lakeside, US 40218</p>
      </div>
    </section>
  </main>
</body>
</html>
```